Tolbek cards

I want a simple business card that pops.
Logo on one side.
On side two i want.
"Are you thinking about a new building on your property, or renovating an existing structure? Contact".....
Owners Name: Dale Whitacre
Owners Phone number: 610-555-0187
Address:4076 Copper Ridge RD, Harlow Springs, PA 16981
Committed to Quality, Service, and Integrity

```html
<!DOCTYPE html>
<html lang="en">
<head>
<meta charset="utf-8">
<title>Tolbek Builders LLC – Business Cards</title>
<link rel="stylesheet" href="https://fonts.googleapis.com/css2?family=Arimo:wght@400;700&family=Kalam:wght@400&display=swap">
<style>
  :root {
    --backdrop: #2b2b2b;
    --card: #f1f1ef;
    --brown-dark: #4a3426;
    --brown-tan: #8d7458;
    --band-light: #8f785f;
    --band-dark: #5b4535;
    --band-text: #f3ece4;
    --rule: #c9b9a6;
  }
  * { margin: 0; padding: 0; box-sizing: border-box; }
  html, body { width: 1200px; height: 576px; overflow: hidden; }
  body {
    background: var(--backdrop);
    position: relative;
    font-family: "Arimo", Arial, sans-serif;
  }
  .card {
    position: absolute;
    background: var(--card);
    border-radius: 10px;
    overflow: hidden;
    box-shadow: 0 4px 12px rgba(0,0,0,0.45);
  }
  .card--front { left: 102px; top: 139px; width: 484px; height: 293px; }
  .card--back  { left: 596px; top: 138px; width: 480px; height: 291px; }

  .wordmark__name,
  .wordmark__sub {
    position: absolute;
    left: 0; right: 0;
    text-align: center;
    color: var(--brown-dark);
    font-weight: 700;
    line-height: 1;
    text-transform: uppercase;
    white-space: nowrap;
  }

  .card--front .wordmark__name { top: 144px; font-size: 50px; letter-spacing: 4px; }
  .card--front .wordmark__sub  { top: 193px; font-size: 17px; letter-spacing: 2.5px; }

  .card--back .wordmark__name { top: 35px; font-size: 36px; letter-spacing: 3px; }
  .card--back .wordmark__sub  { top: 68px; font-size: 12.5px; letter-spacing: 5px; }

  .pitch {
    position: absolute;
    top: 101px; left: 0; right: 0;
    text-align: center;
    font-family: "Kalam", cursive;
    font-size: 17.5px;
    line-height: 23px;
    color: var(--brown-dark);
  }
  .contact-rule {
    position: absolute;
    top: 158px; left: 46px; right: 46px;
    display: flex; align-items: center; gap: 10px;
    font-size: 9.5px; color: var(--brown-dark);
  }
  .contact-rule::before, .contact-rule::after {
    content: ""; flex: 1; height: 1px; background: var(--rule);
  }
  .owner {
    position: absolute; top: 178px; left: 0; right: 0;
    text-align: center; font-size: 21px; font-weight: 700;
    text-transform: uppercase; color: var(--brown-dark);
  }
  .owner__last { color: var(--brown-tan); }
  .phone {
    position: absolute; top: 205px; left: 0; right: 0;
    text-align: center; font-size: 14px; font-weight: 700; color: var(--brown-dark);
  }
  .address {
    position: absolute; top: 225px; left: 0; right: 0;
    text-align: center; font-size: 12.5px; color: var(--brown-tan);
  }
  .tagline-band {
    position: absolute; left: 0; right: 0; bottom: 0;
    height: 31px;
    background: linear-gradient(90deg, var(--band-light), var(--band-dark));
    color: var(--band-text);
    font-size: 13px;
    display: flex; align-items: center; justify-content: center;
  }
</style>
</head>
<body>
  <section class="card card--front" aria-label="Card front">
    <span class="wordmark__name">Tolbek</span>
    <span class="wordmark__sub">Builders LLC</span>
    <div class="tagline-band">Committed to Quality, Service &amp; Integrity</div>
  </section>

  <section class="card card--back" aria-label="Card back">
    <span class="wordmark__name">Tolbek</span>
    <span class="wordmark__sub">Builders LLC</span>
    <p class="pitch">Are you thinking about a new building on your<br>property, or renovating an existing structure?</p>
    <div class="contact-rule">Contact:</div>
    <p class="owner">Dale <span class="owner__last">Whitacre</span></p>
    <p class="phone">Call: 610-555-0187</p>
    <p class="address">Add.: 4076 Copper Ridge RD, Harlow Springs, PA 16981</p>
    <div class="tagline-band">Committed to Quality, Service &amp; Integrity</div>
  </section>
</body>
</html>
```